larkforge website

commerce website to sell cookeries, brackets, mailboxes and to show off homes built. Modern Steel in design see marlo cycles web page to be like: https://www.marlocycles-demo.com/en/ sorry its bright nest hosting word press divi

must be able to add products to page

Target Market(s)

mainly western states of U.S.

Industry/Entity Type

Building Product

Coding

Coded - Design and coding required

Number of Pages Required

3 page

Font styles to use
Sans Serif

Colors

Designer to choose colors to be used in the design.

Requirements
Must have
• customers to be able to order products from page
• bright nest hosting word press divi

```html
<!DOCTYPE html>
<html lang="en">
<head>
<meta charset="utf-8">
<title>Larkforge — Outdoor Firepit Cookery</title>
<link rel="stylesheet" href="https://fonts.googleapis.com/css2?family=Montserrat:wght@400;500;600;700&family=Lato:wght@400;700&family=Quicksand:wght@500;600&family=Roboto:wght@400;500&display=swap">
<style>
:root{
  --navy:#1d2f5f;
  --navy-deep:#152450;
  --navy-btn:#2f4679;
  --footer:#31467a;
  --footer-bar:#253a69;
  --ink:#222;
  --muted:#555;
  --light-blue:#7393cc;
  --faq-ink:#1e3270;
  --green:#5cb531;
  --white:#fff;
}
*{box-sizing:border-box;margin:0;padding:0}
html,body{width:1200px;height:3719px;overflow:hidden}
body{position:relative;background:var(--white);font-family:'Lato',sans-serif;color:var(--ink)}
.abs{position:absolute}
.center{text-align:center}

/* header */
.site-header{position:absolute;left:0;top:0;width:1200px;height:123px;background:var(--white)}
.nav-link{position:absolute;top:62px;font-family:'Roboto',sans-serif;font-size:15px;color:#222;letter-spacing:.2px}
.nav-link.active{font-weight:500;color:var(--navy)}
.nav-link.active::after{content:"";position:absolute;left:0;right:0;bottom:-10px;height:2px;background:var(--navy)}
.brand{position:absolute;left:470px;top:64px;width:250px;text-align:center;font-family:'Montserrat',sans-serif;font-weight:500;font-size:29px;color:var(--navy);letter-spacing:1px}
.brand-mark{position:absolute;left:575px;top:14px;width:40px;height:40px;border-radius:50%;background:var(--navy)}
.cart-count{position:absolute;left:1124px;top:50px;width:22px;height:22px;border-radius:50%;background:#111;color:#fff;font:700 12px/22px 'Roboto',sans-serif;text-align:center}

/* hero */
.hero{position:absolute;left:0;top:123px;width:1200px;height:597px;background:linear-gradient(90deg,#142454 0%,#1c2f5e 40%,#4b5a5a 58%,#6f4a22 72%,#c8772a 86%,#8a4d1c 100%)}
.hero-title{position:absolute;left:150px;top:220px;width:560px;text-align:center;font-family:'Montserrat',sans-serif;font-weight:700;font-size:37px;line-height:43px;color:#fff}
.btn-outline-light{position:absolute;left:328px;top:326px;width:177px;height:46px;border:3px solid #fff;border-radius:24px;color:#fff;font:700 15px/40px 'Montserrat',sans-serif;text-align:center}

/* about */
.about-img{position:absolute;left:100px;top:770px;width:515px;height:332px;background:radial-gradient(ellipse at 50% 45%,#3b3f45 0%,#5a6068 35%,#c9d0dc 60%,#fff 80%)}
.section-title{font-family:'Montserrat',sans-serif;font-weight:400;font-size:28px;color:#222;letter-spacing:.3px}
.section-title b{font-weight:700}
.about-copy{position:absolute;left:652px;top:880px;width:450px;font-family:'Roboto',sans-serif;font-size:14.5px;line-height:25.5px;color:#444}
.about-copy p{margin-bottom:11px}
.btn-outline{position:absolute;border:2.5px solid var(--navy);border-radius:24px;color:var(--navy);font-family:'Montserrat',sans-serif;font-weight:700;text-align:center}

/* featured */
.featured{position:absolute;left:0;top:1216px;width:1200px;height:557px;background:linear-gradient(135deg,#c9ccd2 0%,#eef0f3 40%,#d3d6dc 70%,#bfc3ca 100%)}
.card{position:absolute;background:#fff;box-shadow:0 2px 8px rgba(0,0,0,.12);text-align:center}
.card-img{position:absolute;left:0;top:0;width:100%;background:linear-gradient(160deg,#3a3532 0%,#6a4426 45%,#d06a1c 70%,#2e2a28 100%)}
.card-name{position:absolute;left:0;width:100%;font:600 14px 'Montserrat',sans-serif;color:#222}
.card-desc{position:absolute;left:0;width:100%;font:400 10.5px 'Roboto',sans-serif;color:#555}
.card-price{position:absolute;left:0;width:100%;font:500 17px 'Roboto',sans-serif;color:#222}
.card-btn{position:absolute;border:2.5px solid var(--navy-btn);border-radius:20px;font:700 11px 'Montserrat',sans-serif;color:var(--navy-btn)}
.card-btn.solid{background:var(--navy-btn);color:#fff}

/* categories */
.cat-img{position:absolute;top:1830px;height:273px;background:linear-gradient(170deg,#2a2420 0%,#6b3a1e 50%,#e0691b 72%,#2b2522 100%)}
.cat-box{position:absolute;top:2028px;width:254px;height:146px;background:#fff;border:6px solid var(--light-blue);text-align:center}
.cat-box.dark{border-color:var(--navy-btn)}
.cat-box h3{margin-top:36px;font:700 17.5px 'Montserrat',sans-serif;color:#222;letter-spacing:.3px}
.cat-box p{margin-top:10px;font:400 11.5px/19px 'Roboto',sans-serif;color:#444}

/* testimonial */
.testimonial{position:absolute;left:0;top:2268px;width:1200px;height:487px;background:linear-gradient(135deg,#14255a 0%,#203670 50%,#172a5f 100%);color:#fff}
.quote{position:absolute;left:240px;top:176px;width:720px;text-align:center;font:500 17.5px/26px 'Quicksand',sans-serif}
.quote-mark{position:absolute;font:700 46px 'Georgia',serif;color:#fff}
.avatar{position:absolute;border-radius:50%;border:3px solid #fff}
.author{position:absolute;left:0;width:1200px;text-align:center;font-family:'Quicksand',sans-serif}

/* faq */
.faq-item{position:absolute;left:229px;width:763px;border:2px solid #6a86bf;background:#fff}
.faq-q{position:absolute;left:22px;font:500 16.5px 'Lato',sans-serif;color:var(--faq-ink)}
.faq-a{position:absolute;left:22px;top:54px;width:720px;font:400 14px/19px 'Lato',sans-serif;color:#3a56a0}
.faq-toggle{position:absolute;right:16px;font:400 26px 'Roboto',sans-serif;color:#4a6ab5}

/* footer */
.site-footer{position:absolute;left:0;top:3333px;width:1200px;height:327px;background:var(--footer);color:#fff}
.f-head{position:absolute;font:700 15.5px 'Roboto',sans-serif;letter-spacing:.2px}
.f-list{position:absolute;list-style:none;font:400 14px/25px 'Roboto',sans-serif}
.newsletter-input{position:absolute;left:749px;top:110px;width:313px;height:43px;border-radius:22px;background:#fff;color:#444;font:400 14px/43px 'Roboto',sans-serif;padding-left:24px}
.subscribe{position:absolute;left:753px;top:164px;width:151px;height:43px;border-radius:22px;background:var(--green);color:#fff;font:500 15px/43px 'Roboto',sans-serif;text-align:center}
.pay{position:absolute;top:238px;width:33px;height:21px;border-radius:2px;background:#e9ecf2}
.social{position:absolute;top:240px;width:16px;height:16px;border-radius:50%;border:2px solid #fff}
.footer-bar{position:absolute;left:0;top:3660px;width:1200px;height:59px;background:var(--footer-bar);color:#fff;font:400 13px/59px 'Roboto',sans-serif;text-align:center}
</style>
</head>
<body>

<header class="site-header">
  <a class="nav-link active" style="left:148px">HOME</a>
  <a class="nav-link" style="left:227px">ABOUT US</a>
  <a class="nav-link" style="left:334px">OUR PRODUCTS</a>
  <span class="brand-mark"></span>
  <div class="brand">LARKFORGE</div>
  <a class="nav-link" style="left:728px">SHOP</a>
  <a class="nav-link" style="left:803px">REVIEWS</a>
  <a class="nav-link" style="left:902px">CONTACT US</a>
  <svg class="abs" style="left:1042px;top:61px" width="18" height="18" viewBox="0 0 18 18" fill="none" stroke="#333" stroke-width="1.8"><circle cx="7.5" cy="7.5" r="5.5"/><line x1="11.5" y1="11.5" x2="16" y2="16"/></svg>
  <svg class="abs" style="left:1077px;top:59px" width="18" height="20" viewBox="0 0 18 20" fill="none" stroke="#333" stroke-width="1.6"><circle cx="9" cy="6" r="4"/><path d="M2 19c0-4 3-7 7-7s7 3 7 7"/></svg>
  <svg class="abs" style="left:1108px;top:60px" width="24" height="20" viewBox="0 0 24 20" fill="none" stroke="#333" stroke-width="1.6"><path d="M1 2h4l3 11h12l2-8H7"/><circle cx="9" cy="17" r="1.6"/><circle cx="18" cy="17" r="1.6"/></svg>
  <span class="cart-count">0</span>
</header>

<section class="hero">
  <div class="abs" style="left:620px;top:0;width:580px;height:597px" role="img" aria-label="Photo of a round steel mesh fire pit burning logs on a garden lawn"></div>
  <h1 class="hero-title">BEST QUALITY OUTDOOR FIREPIT COOKERY</h1>
  <a class="btn-outline-light">BUY NOW</a>
  <svg class="abs" style="left:74px;top:255px" width="32" height="60" viewBox="0 0 32 60" fill="none" stroke="#fff" stroke-width="3"><path d="M28 2L4 30l24 28"/></svg>
  <svg class="abs" style="left:1100px;top:255px" width="32" height="60" viewBox="0 0 32 60" fill="none" stroke="#fff" stroke-width="3" opacity=".6"><path d="M4 2l24 28L4 58"/></svg>
</section>

<section>
  <div class="about-img" role="img" aria-label="Photo of a steel fire bowl with mesh lid on a pedestal, set before a pale winged emblem"></div>
  <h2 class="section-title abs" style="left:654px;top:826px">ABOUT <b>LARKFORGE</b></h2>
  <div class="about-copy">
    <p>Nunc tempus felis vitae urna Vivamus porttitor neque at volutpat rutrum purus nisi eleifend libero a tempus libero lectus</p>
    <p>Aeugiat felis Morbi diam mauris viverra in gravida eu mattis in ante Morbi eget arcu Morbi porta libero id ullamcorper nonummy nibh ligula pulvinar metus eget consectetu</p>
  </div>
  <a class="btn-outline" style="left:652px;top:1046px;width:163px;height:47px;font-size:14px;line-height:42px">LEARN MORE</a>
</section>

<section class="featured">
  <h2 class="section-title abs center" style="left:0;top:43px;width:1200px;font-size:26px;color:#333">FEATURED <b>PRODUCTS</b></h2>

  <article class="card" style="left:99px;top:115px;width:233px;height:333px">
    <div class="card-img" style="height:174px" role="img" aria-label="Photo of a tall black fire basket with glowing coals"></div>
    <div class="card-name" style="top:213px">COOKERY</div>
    <div class="card-desc" style="top:236px">Atus eget consectetuer augue</div>
    <div class="card-price" style="top:255px">$25.99</div>
    <a class="card-btn" style="left:54px;top:292px;width:133px;height:35px;line-height:30px">BUY NOW</a>
  </article>

  <article class="card" style="left:354px;top:97px;width:257px;height:382px">
    <div class="card-img" style="height:208px" role="img" aria-label="Photo of a grill grate over burning wood in a steel pit"></div>
    <div class="card-name" style="top:240px;font-size:15px">COOKERY</div>
    <div class="card-desc" style="top:265px;font-size:11.5px">Atus eget consectetuer augue</div>
    <div class="card-price" style="top:285px;font-size:18px">$35.99</div>
    <a class="card-btn solid" style="left:58px;top:318px;width:147px;height:39px;line-height:34px">BUY NOW</a>
  </article>

  <article class="card" style="left:630px;top:121px;width:232px;height:341px">
    <div class="card-img" style="height:174px" role="img" aria-label="Photo of a fire pit with burning logs and grate"></div>
    <div class="card-name" style="top:213px">COOKERY</div>
    <div class="card-desc" style="top:236px">Atus eget consectetuer augue</div>
    <div class="card-price" style="top:255px">$35.99</div>
    <a class="card-btn" style="left:51px;top:288px;width:133px;height:35px;line-height:30px">BUY NOW</a>
  </article>

  <article class="card" style="left:884px;top:121px;width:232px;height:341px">
    <div class="card-img" style="height:174px;background:linear-gradient(170deg,#5e6d78 0%,#8a8f80 40%,#b75a1e 60%,#3e3b33 100%)" role="img" aria-label="Photo of a wide fire bowl on legs beside a lake"></div>
    <div class="card-name" style="top:213px">COOKERY</div>
    <div class="card-desc" style="top:236px">Atus eget consectetuer augue</div>
    <div class="card-price" style="top:255px">$35.99</div>
    <a class="card-btn" style="left:54px;top:288px;width:133px;height:35px;line-height:30px">BUY NOW</a>
  </article>
</section>

<section>
  <div class="cat-img" style="left:86px;width:334px" role="img" aria-label="Photo of flames inside a brick oven"></div>
  <div class="cat-img" style="left:433px;width:334px" role="img" aria-label="Photo of a steel grill grate above glowing embers"></div>
  <div class="cat-img" style="left:781px;width:334px;height:268px;background:linear-gradient(170deg,#4c4a46 0%,#9ea2a6 40%,#3a3a38 70%,#2a2826 100%)" role="img" aria-label="Photo of a camp stove fire beside a tent"></div>

  <div class="cat-box" style="left:128px"><h3>NEW COOKERIES</h3><p>Lorem ipsum dolor sit amet cons<br>ectetuer adipiscing elit</p></div>
  <div class="cat-box dark" style="left:474px"><h3>TOP COOKERIES</h3><p>Lorem ipsum dolor sit amet cons<br>ectetuer adipiscing elit</p></div>
  <div class="cat-box" style="left:821px"><h3>COOKERIES</h3><p>Lorem ipsum dolor sit amet cons<br>ectetuer adipiscing elit</p></div>
</section>

<section class="testimonial">
  <h2 class="section-title abs center" style="left:0;top:74px;width:1200px;color:#fff;font-size:26px">WHAT PEOPLE <b>SAYS</b></h2>
  <svg class="abs" style="left:528px;top:142px" width="144" height="24" viewBox="0 0 144 24" fill="#fff">
    <g id="star"><path d="M12 1l3.2 7 7.6.7-5.8 5 1.8 7.5L12 17.4 5.2 21.2 7 13.7 1.2 8.7l7.6-.7z"/></g>
    <use href="#star" x="30"/><use href="#star" x="60"/><use href="#star" x="90"/><use href="#star" x="120"/>
  </svg>
  <span class="quote-mark" style="left:218px;top:162px">“</span>
  <p class="quote">Oren and his crew are customer-oriented knowledgeable and trustworthy profes­sionals who make the process of getting a new roof a nonevent in my book. They make themselves available around the clock to answer</p>
  <span class="quote-mark" style="left:828px;top:222px">”</span>
  <div class="avatar" style="left:477px;top:280px;width:60px;height:60px;background:#c9c9c9" role="img" aria-label="Customer portrait"></div>
  <div class="avatar" style="left:554px;top:268px;width:80px;height:80px;background:#9fb3c8" role="img" aria-label="Customer portrait"></div>
  <div class="avatar" style="left:651px;top:280px;width:60px;height:60px;background:#8a8a8a;border-color:#5b6a88" role="img" aria-label="Customer portrait"></div>
  <div class="author" style="top:364px;font-size:17.5px;font-weight:500">By Author Name</div>
  <div class="author" style="top:392px;font-size:12px;font-weight:500">City Location</div>
</section>

<section>
  <h2 class="section-title abs center" style="left:0;top:2822px;width:1200px;font-size:28px;color:#333">QUESTIONS AND <b>ANSWER</b></h2>

  <div class="faq-item" style="top:2903px;height:55px"><span class="faq-q" style="top:16px">Nunc tempus felis vitae urna Vivamus porttitor ?</span><span class="faq-toggle" style="top:10px">+</span></div>
  <div class="faq-item" style="top:2968px;height:55px"><span class="faq-q" style="top:16px">Phasellus pellentesque aliquam enim Proin dui lectus cursus?</span><span class="faq-toggle" style="top:10px">+</span></div>
  <div class="faq-item" style="top:3033px;height:108px">
    <span class="faq-q" style="top:16px">Morbi eget arcu Morbi porta libero ?</span><span class="faq-toggle" style="top:4px">–</span>
    <p class="faq-a">Pellentesque faucibus Ut accumsan ultricies elit Maecenas at justo id velit placerat molestie Donec dictum lectus non odio Cras a ante vitae enim iaculis aliquam Mauris nunc quam venenatis nec</p>
  </div>
  <div class="faq-item" style="top:3176px;height:55px"><span class="faq-q" style="left:24px;top:16px;font-size:16px">Fusce tellus Sed metus augue convallis et vehicula?</span><span class="faq-toggle" style="top:10px">+</span></div>
  <div class="faq-item" style="top:3239px;height:55px"><span class="faq-q" style="left:24px;top:16px;font-size:16px">Nunc tempus felis vitae urna Vivamus porttitor neque ?</span><span class="faq-toggle" style="top:12px">+</span></div>
</section>

<footer class="site-footer">
  <h4 class="f-head" style="left:160px;top:73px">QUICK LINKS</h4>
  <ul class="f-list" style="left:160px;top:112px"><li>Home</li><li>About Us</li><li>Products</li><li>Shop</li><li>Contact Us</li></ul>

  <h4 class="f-head" style="left:345px;top:73px">RESOURCES</h4>
  <ul class="f-list" style="left:347px;top:115px"><li>My Basket</li><li>Wishlist</li><li>Account</li><li>Support</li><li>FAQ</li></ul>

  <h4 class="f-head" style="left:524px;top:74px">CONTACT US</h4>
  <ul class="f-list" style="left:524px;top:112px"><li>214 W 42nd Street #B</li><li>Texas 75001 TX</li><li>(555) 010 4821</li><li>hello@larkforge-demo.com</li></ul>
  <span class="social" style="left:523px"></span>
  <span class="social" style="left:568px"></span>
  <span class="social" style="left:614px"></span>
  <span class="social" style="left:660px"></span>

  <h4 class="f-head" style="left:754px;top:70px">NEWSLETTER SIGN UP</h4>
  <div class="newsletter-input">Email address</div>
  <div class="subscribe">SUBSCRIBE</div>
  <span class="pay" style="left:766px"></span>
  <span class="pay" style="left:815px"></span>
  <span class="pay" style="left:865px"></span>
  <span class="pay" style="left:915px"></span>
</footer>
<div class="footer-bar">© 2020 Company Name&nbsp; All right reserved</div>

</body>
</html>
```